Catering Menu Package

I currently have a complete menu package, which we have redesigned as far as content, now I need to it put together in a catalog type format. It is essentially 10-12 pages in length, and will be sent for print production. Upon receiving a final edit
Updates

I have added an example gif to the project.

I did this free hand this basically what I am looking for. please change text and type to whatever you think would look best. This is a total rough design so, feel free to change any and everything. The text for the page is on the word documents. If you need more images let me know I am in the process of getting as many images uploaded for your use.

Project Deadline Extended
Reason: I figured we got a late jump with questions, so i am extending a few days .

Target Market(s)

The target market is business who wish to have catered luncheons, breakfasts , meetings

Industry/Entity Type

Catering

Requirements
Must have
• I have attached a copy of the text that what we want in the package, our logo, and i have also attached a catering package of another company to give you an idea what the finished product will be
Should not have
• It should not look identical to the example catering packages, these are for some inspiration we want our own design with the same type of look and feel

```html
<!DOCTYPE html>
<html lang="en">
<head>
<meta charset="utf-8">
<title>Light Breakfast — Harrow Field Caterers</title>
<link rel="stylesheet" href="https://fonts.googleapis.com/css2?family=UnifrakturMaguntia&family=Pinyon+Script&family=Amaranth:ital@0;1&display=swap">
<style>
  :root {
    --paper: #ece7dc;
    --paper-deep: #e3ddd0;
    --ink: #111111;
    --text: #2a2622;
    --bread-light: #e7d6b6;
    --bread-mid: #c79a62;
    --bread-dark: #8a5a2e;
    --logo-ink: #1a1a1a;
  }
  * { margin: 0; padding: 0; box-sizing: border-box; }
  html, body { width: 1200px; height: 928px; overflow: hidden; background: #ffffff; }
  .menu-page {
    position: relative;
    width: 1200px;
    height: 928px;
    overflow: hidden;
    background: var(--paper);
    font-family: "Amaranth", "Georgia", serif;
    color: var(--text);
  }
  .paper-texture {
    position: absolute;
    left: 0; top: 0;
    width: 712px; height: 928px;
    background: radial-gradient(ellipse at 40% 50%, var(--paper) 0%, var(--paper-deep) 100%);
  }
  .bread-photo {
    position: absolute;
    left: 712px; top: 0;
    width: 488px; height: 928px;
    background:
      radial-gradient(ellipse at 30% 12%, var(--bread-light) 0%, transparent 38%),
      radial-gradient(ellipse at 55% 42%, var(--bread-mid) 0%, transparent 45%),
      radial-gradient(ellipse at 35% 80%, var(--bread-light) 0%, transparent 40%),
      linear-gradient(160deg, var(--bread-mid) 0%, var(--bread-dark) 55%, var(--bread-mid) 100%);
  }
  .page-title {
    position: absolute;
    right: 500px;
    top: 8px;
    font-family: "UnifrakturMaguntia", "Times New Roman", serif;
    font-weight: 400;
    font-size: 62px;
    line-height: 1;
    color: var(--ink);
  }
  .title-rule {
    position: absolute;
    left: 46px; top: 78px;
  }
  .menu-list {
    position: absolute;
    right: 504px;
    top: 0;
    width: 640px;
    text-align: right;
  }
  .menu-item { position: absolute; right: 0; width: 640px; }
  .item-name {
    font-family: "Pinyon Script", "Brush Script MT", cursive;
    font-weight: 400;
    font-size: 44px;
    line-height: 1;
    color: var(--ink);
    margin-bottom: 4px;
  }
  .item-desc {
    font-size: 17.5px;
    line-height: 29px;
  }
  .item-quick { top: 104px; }
  .item-fast { top: 224px; }
  .item-lean { top: 374px; }
  .item-newyorker { top: 480px; }
  .item-city { top: 668px; }
  .fine-print {
    position: absolute;
    right: 508px;
    top: 864px;
    text-align: right;
    font-style: italic;
    font-size: 12.5px;
    line-height: 12px;
  }
  .brand-mark {
    position: absolute;
    left: 1070px;
    top: 720px;
    width: 96px;
    text-align: center;
  }
  .brand-mark .brand-dot {
    display: block;
    width: 64px; height: 64px;
    margin: 0 auto 10px;
    border-radius: 50%;
    background: #ffffff;
  }
  .brand-mark .brand-name {
    font-size: 15px;
    line-height: 16px;
    color: var(--logo-ink);
  }
</style>
</head>
<body>
<main class="menu-page">
  <div class="paper-texture" role="img" aria-label="Cream background with soft swirling damask pattern"></div>
  <div class="bread-photo" role="img" aria-label="Close-up photograph of golden baked breakfast rolls"></div>

  <h1 class="page-title">Light Breakfast</h1>
  <svg class="title-rule" width="656" height="8" viewBox="0 0 656 8" aria-hidden="true">
    <polygon points="0,3 656,0 656,7 0,4" fill="#111111"/>
  </svg>

  <section class="menu-list">
    <article class="menu-item item-quick">
      <h2 class="item-name">Quick and Easy</h2>
      <p class="item-desc">French Pastry, a Fresh Baked Gourmet Muffin, and Whole Fresh Fruit<br>(Featuring Local Apples and Peaches, California Oranges, or Bananas)</p>
    </article>
    <article class="menu-item item-fast">
      <h2 class="item-name">Fast Farmhouse</h2>
      <p class="item-desc">Fresh baked Breakfast Bread and Buttery Biscuits, Whipped Butter and<br>House-made Strawberry Jam and Local Fruit Jellies, and Whole Fresh Fruit<br>(Featuring Local Apples and Peaches, California Oranges, or Bananas).</p>
    </article>
    <article class="menu-item item-lean">
      <h2 class="item-name">Light and Lean</h2>
      <p class="item-desc">Individual Yogurt, Fresh Fruit and Berry Cups and House-made Granola.</p>
    </article>
    <article class="menu-item item-newyorker">
      <h2 class="item-name">New Yorker</h2>
      <p class="item-desc">Brooklyn Bagel, Whipped Cream Cheese, House-made Strawberry Jam and<br>Local Fruit Jellies, Whipped Butter, and Whole Fresh Fruit<br>(Featuring Local Apples and Peaches, California Oranges, or Bananas)<br>Add Smoked Salmon</p>
    </article>
    <article class="menu-item item-city">
      <h2 class="item-name">City Farmhouse</h2>
      <p class="item-desc">Fresh Baked Buttery Biscuits, Gourmet Muffins and Breakfast Breads,<br>Brooklyn Bagels, Whole Fresh Fruit (Featuring Local Apples and Peaches,<br>California Oranges, or Bananas), Whipped Butter and Cream Cheese,<br>House-made Strawberry Jam and Local Fruit Jellies.</p>
    </article>
  </section>

  <p class="fine-print">All Prices are per Person, with a 10 person minimum order per item chosen.<br>Local Products used when available and in season</p>

  <div class="brand-mark">
    <span class="brand-dot"></span>
    <span class="brand-name">harrow field<br>caterers</span>
  </div>
</main>
</body>
</html>
```